Lurvik.no is a new website about pedagogical entrepreneurship. It's main target group is teachers. The Nordic Bureau for Digital Schooling and the National Office for Learning and Classrooms are leading the project.

The web page is meant to show examples of how different methods of entrepreneurship can be used pedagogical in a learning environment. The page will also support the user with examples of different teaching programs and other examples of best practice.

Pedagogical entrepreneurship is not about business and men in suits. It's a method for learning. The focus in the design should be on school, education and new ways of learning.

The final product should be motivating and engaging, but at the same time governmental and serious. We are not looking for something "flashy" and corporate-looking, but a moderate, task-focused and clean design that state quality.

We need designs for three pages:
1 - frontpage
2 - subpage ("Metoder og undervisningsopplegg")
3 - subpage ("Små-TOPP i Vassbygd")

The interaction design for these three pages will be uploaded as an attachment.

We would like you to find inspiration in the following websites:
- www.skapekraft.no
- www.giellu.no
- www.brightfernlab.com
- www.zyx.no
(more will be added)

Please use the attached logo, and feel free to use this as an inspiration for the rest of the design.

Target Market(s)

Teachers

Industry/Entity Type

Education

Requirements
Must have
• * Header with: Logo. Main navigation. Utility navigation. Search box.
* Footer
Should not have
• Images of men in suits.
Very strong graphical elements that stands out too much (we want it clean).

```html
<!DOCTYPE html>
<html lang="en">
<head>
<meta charset="utf-8">
<title>Lurvik.no – Pedagogical entrepreneurship</title>
<link rel="stylesheet" href="https://fonts.googleapis.com/css2?family=Asap:wght@400;500;700&display=swap">
<style>
  :root {
    --navy: #0f4f8c;
    --blue: #1a6fb5;
    --blue-mid: #2f8ccf;
    --sky: #8cc8ec;
    --sky-light: #d4ecf9;
    --cyan: #29a8df;
    --ink: #123f6e;
    --grey: #5d6670;
    --white: #ffffff;
    --green: #3a9a2e;
  }
  * { box-sizing: border-box; margin: 0; padding: 0; }
  html, body { width: 1200px; height: 900px; overflow: hidden; }
  body {
    font-family: "Asap", Arial, sans-serif;
    background: linear-gradient(180deg, var(--white) 0, var(--white) 360px, var(--sky-light) 470px, var(--sky) 640px, #6fb3e2 900px);
    color: var(--ink);
    position: relative;
  }
  .top-stripe { position: absolute; top: 0; left: 0; width: 100%; height: 5px; background: var(--navy); }

  /* header */
  .site-header { position: absolute; top: 5px; left: 0; width: 100%; height: 100px; }
  .brand { position: absolute; left: 140px; top: 28px; display: flex; align-items: center; gap: 12px; }
  .brand-dot { width: 40px; height: 40px; border-radius: 50%; background: var(--blue); }
  .brand-name { font-size: 42px; font-weight: 500; color: var(--blue); letter-spacing: -0.5px; }
  .main-nav { position: absolute; left: 560px; top: 14px; display: flex; gap: 28px; font-size: 13px; font-weight: 700; }
  .main-nav a { color: var(--ink); text-decoration: none; }
  .main-nav a.active { text-decoration: underline; }
  .search-box {
    position: absolute; left: 890px; top: 0; width: 160px; height: 34px;
    background: var(--navy); color: #9fc3e3; font-size: 12px;
    display: flex; align-items: center; justify-content: space-between; padding: 0 10px;
    border-radius: 0 0 4px 4px;
  }

  /* hero */
  .hero-photo {
    position: absolute; left: 690px; top: 38px; width: 360px; height: 300px;
    background: radial-gradient(ellipse at 65% 40%, #e9d8c0 0, #f1ebe2 40%, rgba(255,255,255,0) 72%);
  }
  .hero-copy { position: absolute; right: 520px; top: 130px; text-align: right; width: 500px; }
  .hero-copy h1 { font-size: 25px; font-weight: 700; color: var(--ink); line-height: 1.15; }
  .hero-copy p { font-size: 14px; color: var(--grey); line-height: 1.7; margin-top: 6px; }

  .wave { position: absolute; left: 0; top: 360px; width: 1200px; height: 180px; }

  /* feature row */
  .features { position: absolute; left: 150px; top: 330px; width: 910px; display: flex; }
  .feature { position: relative; width: 33.33%; height: 130px; padding: 0 8px; }
  .feature + .feature { border-left: 1px dashed #9ccbe8; }
  .feature-icon { position: absolute; left: 10px; top: 10px; width: 70px; height: 70px; }
  .feature-title { position: absolute; left: 88px; top: 6px; font-size: 22px; line-height: 1.22; color: var(--blue); }
  .cta {
    position: absolute; left: 10px; top: 106px; width: 270px; height: 24px;
    background: linear-gradient(180deg, #3a8fd0, var(--navy));
    color: var(--white); font-size: 11px; font-weight: 700; text-transform: uppercase;
    display: flex; align-items: center; padding-left: 8px; border-radius: 2px;
  }
  .cta .arrow { position: absolute; right: -4px; top: -2px; width: 28px; height: 28px; }

  /* panels */
  .panel { position: absolute; top: 545px; background: var(--white); box-shadow: 0 2px 6px rgba(10,60,110,.2); }
  .panel-head { height: 32px; background: linear-gradient(180deg, #2b7fc2, var(--navy)); color: var(--white); font-size: 17px; padding: 5px 10px; }
  .panel-quiz { left: 155px; width: 280px; height: 300px; }
  .panel-start { left: 455px; width: 595px; height: 300px; background: linear-gradient(90deg, var(--white) 60%, #eef2f5); }

  .quiz-icon { position: absolute; left: 14px; top: 62px; width: 76px; height: 76px; }
  .quiz-copy { position: absolute; left: 110px; top: 54px; width: 160px; }
  .quiz-copy h2 { font-size: 19px; font-weight: 700; color: var(--ink); line-height: 1.15; }
  .quiz-copy p { font-size: 13px; color: var(--blue); line-height: 1.3; margin-top: 4px; }
  .quiz-copy .cta { position: relative; left: 0; top: 10px; width: 140px; }

  .start-cols { display: flex; padding: 16px 20px; }
  .start-col { width: 50%; }
  .start-col + .start-col { border-left: 1px dashed #9ccbe8; padding-left: 28px; }
  .start-col h3 { font-size: 21px; font-weight: 700; color: var(--ink); margin-bottom: 6px; }
  .start-col li { list-style: none; font-size: 14px; color: var(--ink); line-height: 1.65; }
  .start-col li::before { content: "» "; }
  .start-col li.current { color: var(--cyan); text-decoration: underline; }
</style>
</head>
<body>
  <div class="top-stripe"></div>

  <header class="site-header">
    <div class="brand"><span class="brand-dot"></span><span class="brand-name">Lurvik</span></div>
    <nav class="main-nav">
      <a class="active" href="#">Best practice shools</a>
      <a href="#">Lurvometer</a>
      <a href="#">About lurvik.no</a>
    </nav>
    <div class="search-box">
      <span>Searching for...</span>
      <svg width="16" height="16" viewBox="0 0 16 16"><circle cx="6.5" cy="6.5" r="4.5" fill="none" stroke="#cfe3f4" stroke-width="2"/><line x1="10" y1="10" x2="15" y2="15" stroke="#cfe3f4" stroke-width="2.5" stroke-linecap="round"/></svg>
    </div>
  </header>

  <div class="hero-photo" role="img" aria-label="Photo of smiling students reading books together"></div>
  <div class="hero-copy">
    <h1>Pedagogical<br>entrepreneurship works.</h1>
    <p>Lorem ipsum dolor sit amet, onsectetur adipiscing elit.<br>Onsectetur adipiscing elit dolor sit dolor sit lorem ipsum.</p>
  </div>

  <svg class="wave" viewBox="0 0 1200 180" preserveAspectRatio="none">
    <defs>
      <linearGradient id="waveFill" x1="0" y1="0" x2="0" y2="1">
        <stop offset="0" stop-color="#bfe2f6"/>
        <stop offset="1" stop-color="#8cc8ec"/>
      </linearGradient>
    </defs>
    <path d="M0 10 Q600 -20 1200 10 L1200 180 L0 180 Z" fill="url(#waveFill)"/>
    <path d="M0 0 Q600 110 1200 0 L1200 0 L0 0 Z" fill="#ffffff"/>
  </svg>

  <section class="features">
    <div class="feature">
      <svg class="feature-icon" viewBox="0 0 70 70">
        <circle cx="40" cy="28" r="20" fill="#e8f5fc" stroke="var(--cyan)" stroke-width="4"/>
        <line x1="26" y1="42" x2="8" y2="60" stroke="var(--navy)" stroke-width="7" stroke-linecap="round"/>
      </svg>
      <div class="feature-title">What is<br>pedagogical<br>entrepreneurship?</div>
      <div class="cta">Learn about what, why and how!
        <svg class="arrow" viewBox="0 0 28 28"><rect x="5" y="5" width="18" height="18" transform="rotate(45 14 14)" fill="var(--navy)"/><path d="M12 9 L17 14 L12 19" fill="none" stroke="#fff" stroke-width="2.5"/></svg>
      </div>
    </div>
    <div class="feature">
      <svg class="feature-icon" viewBox="0 0 70 70">
        <path d="M14 52 L30 36 L40 44 L56 18" fill="none" stroke="var(--blue)" stroke-width="4"/>
        <circle cx="14" cy="52" r="8" fill="#fff" stroke="var(--blue)" stroke-width="4"/>
        <circle cx="30" cy="36" r="6" fill="#fff" stroke="var(--cyan)" stroke-width="4"/>
        <circle cx="40" cy="44" r="6" fill="#fff" stroke="var(--blue)" stroke-width="4"/>
        <circle cx="56" cy="16" r="9" fill="#fff" stroke="var(--cyan)" stroke-width="4"/>
      </svg>
      <div class="feature-title">Methods and<br>teaching plans</div>
      <div class="cta">Plain your lessons!
        <svg class="arrow" viewBox="0 0 28 28"><rect x="5" y="5" width="18" height="18" transform="rotate(45 14 14)" fill="var(--navy)"/><path d="M12 9 L17 14 L12 19" fill="none" stroke="#fff" stroke-width="2.5"/></svg>
      </div>
    </div>
    <div class="feature">
      <div class="feature-icon" role="img" aria-label="Illustration of a green sprouting plant" style="background: radial-gradient(circle at 50% 45%, #5cb848 0, var(--green) 45%, rgba(58,154,46,0) 70%);"></div>
      <div class="feature-title">Good examples,<br>best practice</div>
      <div class="cta">Be inspired!
        <svg class="arrow" viewBox="0 0 28 28"><rect x="5" y="5" width="18" height="18" transform="rotate(45 14 14)" fill="var(--cyan)"/><path d="M12 9 L17 14 L12 19" fill="none" stroke="#fff" stroke-width="2.5"/></svg>
      </div>
    </div>
  </section>

  <section class="panel panel-quiz">
    <div class="panel-head">Test youself!</div>
    <svg class="quiz-icon" viewBox="0 0 76 76">
      <rect x="16" y="16" width="44" height="44" rx="6" transform="rotate(45 38 38)" fill="#fff" stroke="var(--blue)" stroke-width="4"/>
      <rect x="24" y="24" width="28" height="28" fill="none" stroke="var(--cyan)" stroke-width="2" stroke-dasharray="4 3"/>
      <path d="M26 38 L35 47 L54 24" fill="none" stroke="var(--navy)" stroke-width="5" stroke-linecap="round" stroke-linejoin="round"/>
    </svg>
    <div class="quiz-copy">
      <h2>Try the<br>lurvometer!</h2>
      <p>Are you working<br>entrepreneurship like?</p>
      <div class="cta">Start quiz
        <svg class="arrow" viewBox="0 0 28 28"><rect x="5" y="5" width="18" height="18" transform="rotate(45 14 14)" fill="var(--navy)"/><path d="M12 9 L17 14 L12 19" fill="none" stroke="#fff" stroke-width="2.5"/></svg>
      </div>
    </div>
  </section>

  <section class="panel panel-start">
    <div class="panel-head">Get started!</div>
    <div class="start-cols">
      <div class="start-col">
        <h3>Teaching plans</h3>
        <ul>
          <li>Lorem ipsum dolor sit amet</li>
          <li>Onsectetur adipiscing elit</li>
          <li>Onsectetur</li>
          <li>Adipiscing elit dolor sit</li>
          <li>Dolor sit lorem ipsum.</li>
        </ul>
      </div>
      <div class="start-col">
        <h3>Methods</h3>
        <ul>
          <li class="current">Café-pedagogikk</li>
          <li>Elevbedrift</li>
          <li>Gründercamp</li>
          <li>Story line</li>
          <li>Real</li>
        </ul>
      </div>
    </div>
  </section>
</body>
</html>
```